U.S. Popcorn company needs business cards

We are a popcorn company that manufactures popcorn and sells it to grocery stores worldwide. Our theme is "Americana" and our logo is U.S. route 66 which is the most famous highway in the U.S.

We would like the design to be simple and to use both sides. On the back side we would like to see just the logo and website. The front would be normal details

Target Market(s)

Wholesalers, grocers and distributors

Industry/Entity Type

Manufacture

Contact Information for Business Card

Business name: Prairie Lantern Popcorn
Phone: +1 555 308 4726
Email: Dale@prairielanternpopcorn.com
website: www.prairielanternpopcorn.com
Tag Line: "POPped with prairie pride"
Name: Dale Whitcombe
Title: Founder/President

Requirements
Must have
• Either this design should be fun or clean and simple. I will let you show me your thougths.
Nice to have
• Anything that ties in the real Hwy Route 66.
• Colors might need to be red, white and blue incorporated.
Should not have
• Not be too busy.

```html
<!DOCTYPE html>
<html lang="en">
<head>
<meta charset="utf-8">
<title>Prairie Lantern Popcorn – Business Cards</title>
<link href="https://fonts.googleapis.com/css2?family=Open+Sans:ital,wght@0,400;0,600;0,700;1,400&display=swap" rel="stylesheet">
<style>
  :root {
    --navy: #122e63;
    --navy-text: #1b2f66;
    --red: #d0201c;
    --paper: #ffffff;
    --backdrop: #e6e6e6;
    --ink-soft: #2a3b6e;
  }
  * { margin: 0; padding: 0; box-sizing: border-box; }
  html, body {
    width: 1200px; height: 576px; overflow: hidden;
    background: var(--backdrop);
    font-family: "Open Sans", Arial, sans-serif;
  }
  .stage { position: relative; width: 1200px; height: 576px; }

  .card { position: absolute; top: 139px; border-radius: 6px; overflow: hidden; }

  /* Back side */
  .card-back {
    left: 82px; width: 484px; height: 292px;
    background: var(--navy);
  }
  .card-back .brand {
    position: absolute; left: 0; right: 0; top: 100px;
    text-align: center; color: var(--paper);
    font-weight: 700; font-size: 30px; line-height: 1.15;
    letter-spacing: 0.5px;
  }
  .card-back .site-row {
    position: absolute; left: 0; right: 0; top: 256px;
    display: flex; align-items: center; justify-content: center; gap: 10px;
  }
  .card-back .rule { width: 44px; height: 2px; background: var(--red); }
  .card-back .site {
    color: var(--paper); font-weight: 600; font-size: 11.5px; letter-spacing: 0.3px;
  }

  /* Front side */
  .card-front {
    left: 602px; width: 482px; height: 290px;
    background: var(--paper);
  }
  .person { position: absolute; left: 22px; top: 26px; }
  .person .name { color: var(--red); font-weight: 700; font-size: 16.5px; line-height: 1.2; }
  .person .title { color: var(--navy-text); font-style: italic; font-size: 12px; line-height: 1.3; }

  .tagline {
    position: absolute; right: 22px; top: 28px;
    color: var(--navy-text); font-size: 15.5px;
  }
  .tagline .pop { color: var(--red); font-weight: 700; }

  .contacts { position: absolute; left: 26px; top: 192px; list-style: none; }
  .contacts li {
    display: flex; align-items: center; gap: 10px;
    height: 17px; color: var(--ink-soft); font-size: 13px;
  }
  .contacts svg { width: 11px; height: 11px; flex: none; }

  .front-brand {
    position: absolute; left: 312px; top: 170px; width: 154px;
    text-align: center; color: var(--navy);
    font-weight: 700; font-size: 19px; line-height: 1.15;
  }

  .base-band { position: absolute; left: 0; bottom: 0; width: 482px; height: 12px; }
</style>
</head>
<body>
<main class="stage">

  <section class="card card-back" aria-label="Card back">
    <div class="brand">Prairie Lantern<br>Popcorn</div>
    <div class="site-row">
      <span class="rule"></span>
      <span class="site">www.prairielanternpopcorn.com</span>
      <span class="rule"></span>
    </div>
  </section>

  <section class="card card-front" aria-label="Card front">
    <div class="person">
      <p class="name">Dale Whitcombe</p>
      <p class="title">Founder/President</p>
    </div>

    <p class="tagline">"<span class="pop">POP</span>ped with prairie pride"</p>

    <ul class="contacts">
      <li>
        <svg viewBox="0 0 12 12" aria-hidden="true"><path fill="#d0201c" d="M1 4.5C1 3 3 2 6 2s5 1 5 2.5v.8H8.5v-1h-5v1H1zM3 6h6l1.5 4.5h-9z"/><circle cx="6" cy="8" r="1.2" fill="#fff"/></svg>
        +1 555 308 4726
      </li>
      <li>
        <svg viewBox="0 0 12 12" aria-hidden="true"><rect x="0.5" y="2.5" width="11" height="7.5" fill="#d0201c"/><path d="M0.5 2.5 6 7l5.5-4.5" fill="none" stroke="#fff" stroke-width="1"/></svg>
        Dale@prairielanternpopcorn.com
      </li>
      <li>
        <svg viewBox="0 0 12 12" aria-hidden="true"><circle cx="6" cy="6" r="5" fill="#d0201c"/><path d="M1 6h10M6 1v10M3 3.2c2 1 4 1 6 0M3 8.8c2-1 4-1 6 0" fill="none" stroke="#fff" stroke-width="0.8"/></svg>
        www.prairielanternpopcorn.com
      </li>
    </ul>

    <div class="front-brand">Prairie Lantern<br>Popcorn</div>

    <svg class="base-band" viewBox="0 0 482 12" preserveAspectRatio="none" aria-hidden="true">
      <polygon points="0,0 372,0 362,12 0,12" fill="var(--navy)"/>
      <polygon points="376,0 482,0 482,12 366,12" fill="var(--red)"/>
    </svg>
  </section>

</main>
</body>
</html>
```